Dietary supplement, Clean and simple.

Hi,
I’d like to talk about the project,

About us:
We are a dietary supplement (Vitamins, Minerals, amino acids etc.) company.
The goal is to have about 25 products at the end of this year. However, for this goal to be achieved we need a good label design to make our products represent our company values.
I’ll be here every day supporting your questions, we are fully committed to making the highest/best quality/customer experience possible.

About the design and our values:
- Professional (We are in the industry of professionalism and expertise. I would love to show we are competent at this, Id. Like to have the labels looks like we have done our research.)
- Efficient (White spacing, good use of the space available.)
- Simple (Straight forward, in 5 seconds they have to know what the product they have is/how functions. We’re trying to simplify it for the consumer.
- No distractions (the only visually “distracting” factor can be the vector art.)

The guidelines:
The goal is to have a universal design, with one element that changes (Vector art). I’ll attach a file/multiple files I think can show some visuals on what I’m looking for, and what parts of the design I think are good/bad.

Label size: 69x155mm (Front is 77.5mm)

Design whatever you think fits our image. You’re the design expert, all I care about is that it fits our company standards/image.

Use this color/font.
Font: Sans Serif
Main company color is Mind green #237D62 (Use this color for something in the design.)

What I thought would be cool/might looks ugly, who knows:
1. The front of the label: Should have 1 vector art, preferably in the top right corner. (That looks good in multiple colors. The vector can have multiple areas to color, I would prefer 2 main colors in the vector art. The interchangeable colors are used for multiple kinds of products.)
2. Text/product information on the left. The text that will have to be displayed:
- Product name for instance “Magnesium + B6”
- Description for the product for instance “Magnesium with ginger taste”
- Company name or logo. (Add ® behind it. We are soon to be trademark registered.)
3. We need to show the "daily intake" amount on the front and also the amount in the complete bottle. For instance, “Daily intake 1 capsule, 60 capsules”.
• You don’t have to design the backside of the label. After I chose a design, I’d like to chat and give specific information on what areas need to be assigned where. (Too complex because of the law.)
Updates

Hi, Please make the deadline 31 days total. I want designers to have the time to design. And not be rushed to finish it.

I want to extend the deadline because i feel like a slightly more medical look would be interesting. Hope you can come up with something!!

Target Market(s)

Dietary supplement consumers

Industry/Entity Type

Dietary supplements

Font styles to use
Sans Serif

Colors

Designer to choose colors to be used in the design.

Requirements
Must have
• Trademark icon "®" has to be at the top right after the company logo(text of logo)/name.

```html
<!DOCTYPE html>
<html lang="en">
<head>
<meta charset="utf-8">
<title>Kestrel Labs – Magnesium Label</title>
<link href="https://fonts.googleapis.com/css2?family=Montserrat:wght@400;500;600;700;800&display=swap" rel="stylesheet">
<style>
  :root {
    --mint-green: #236E45;
    --leaf-green: #5DA84F;
    --lime: #B8D259;
    --cream: #DCCF7A;
    --ink: #3A3A3A;
    --paper: #FFFFFF;
    --name-start: #A6CC3C;
    --name-end: #6DB344;
  }
  * { margin: 0; padding: 0; box-sizing: border-box; }
  html, body { width: 1200px; height: 535px; overflow: hidden; background: var(--paper); }
  .label {
    position: relative;
    width: 1200px;
    height: 535px;
    font-family: "Montserrat", sans-serif;
    background: var(--paper);
  }
  .label-shapes { position: absolute; inset: 0; }
  .brand {
    position: absolute;
    left: 762px;
    top: 74px;
    transform: translateX(-50%);
    display: flex;
    align-items: center;
    gap: 10px;
  }
  .brand-mark {
    width: 16px; height: 16px;
    background: var(--ink);
  }
  .brand-name {
    font-weight: 600;
    font-size: 26px;
    color: var(--ink);
    white-space: nowrap;
  }
  .product {
    position: absolute;
    left: 671px;
    top: 214px;
    transform: translateX(-50%);
    text-align: center;
  }
  .product-name {
    font-weight: 700;
    font-size: 56px;
    line-height: 1;
    letter-spacing: 0.5px;
    background: linear-gradient(90deg, var(--name-start), #B9C972 40%, var(--name-end));
    -webkit-background-clip: text;
    background-clip: text;
    color: transparent;
  }
  .product-description {
    font-weight: 500;
    font-size: 18px;
    color: var(--ink);
    white-space: nowrap;
  }
  .dosage {
    position: absolute;
    left: 809px;
    top: 338px;
    width: 89px;
    height: 114px;
    background: var(--mint-green);
    border-radius: 20px 0 0 20px;
    color: var(--paper);
    text-align: center;
  }
  .dosage-label { margin-top: 6px; font-size: 12px; font-weight: 500; }
  .dosage-amount { font-size: 40px; font-weight: 800; line-height: 36px; margin-top: 1px; }
  .dosage-unit { font-size: 13px; font-weight: 700; line-height: 16px; }
  .dosage-rule { width: 72px; height: 2px; background: var(--paper); margin: 3px auto 0; }
  .dosage-count { font-size: 16px; font-weight: 700; margin-top: 7px; }
</style>
</head>
<body>
<div class="label">
  <svg class="label-shapes" width="1200" height="535" viewBox="0 0 1200 535" aria-hidden="true">
    <defs>
      <linearGradient id="cream-fade" x1="0" y1="0" x2="1" y2="0.35">
        <stop offset="0" stop-color="var(--cream)" stop-opacity="1"/>
        <stop offset="0.7" stop-color="#FFFFFF" stop-opacity="0"/>
      </linearGradient>
    </defs>
    <rect class="band-top" x="0" y="0" width="1200" height="16" fill="var(--mint-green)"/>
    <rect class="band-bottom" x="0" y="519" width="1200" height="16" fill="var(--mint-green)"/>
    <path class="cream-sweep" d="M514,16 L690,16 C600,70 530,170 540,300 C548,380 580,440 600,487 L566,487 C490,400 426,300 423,200 C422,130 452,60 514,16 Z" fill="url(#cream-fade)"/>
    <path class="lime-sweep" d="M300,16 L514,16 C452,60 422,130 423,200 C426,300 490,400 566,487 L566,519 L300,519 Z" fill="var(--lime)"/>
    <path class="green-panel" d="M300,16 L514,16 C450,60 418,130 419,200 C420,290 470,390 526,487 L526,519 L300,519 Z" fill="var(--leaf-green)"/>
    <path class="base-tab" d="M428,519 L446,494 Q452,487 464,487 L761,487 Q773,487 779,494 L793,519 Z" fill="var(--mint-green)"/>
  </svg>

  <div class="brand">
    <span class="brand-mark"></span>
    <span class="brand-name">Kestrel Labs</span>
  </div>

  <div class="product">
    <h1 class="product-name">MAGNESIUM</h1>
    <p class="product-description">Magnesium with lemon taste</p>
  </div>

  <div class="dosage">
    <p class="dosage-label">take daily</p>
    <p class="dosage-amount">01</p>
    <p class="dosage-unit">capsule</p>
    <div class="dosage-rule"></div>
    <p class="dosage-count">60 Caps</p>
  </div>
</div>
</body>
</html>
```